The Plate Compass

Cutting Through the Noise to What Actually Works.

Nutrition book

Target Market(s)

People looking to be or get healthy and eat right.

```html
<!DOCTYPE html>
<html lang="en">
<head>
<meta charset="UTF-8">
<title>The Plate Compass — Book Cover</title>
<link href="https://fonts.googleapis.com/css2?family=Montserrat:wght@400;500;800;900&display=swap" rel="stylesheet">
<style>
  :root {
    --paper: #f7f4ee;
    --navy: #0d2940;
    --green: #2e8a0c;
    --ink: #1f2a33;
    --white: #ffffff;
    --tier-1: #e8482a;
    --tier-2: #dea019;
    --tier-3: #4cbf1a;
    --tier-4: #2fb08c;
    --tier-5: #1a56b8;
    --tier-6: #2c3a45;
  }
  * { margin: 0; padding: 0; box-sizing: border-box; }
  html, body { width: 800px; height: 1200px; overflow: hidden; background: var(--paper); }
  .cover {
    position: relative;
    width: 800px; height: 1200px;
    background: var(--paper);
    font-family: "Montserrat", sans-serif;
    overflow: hidden;
  }
  .title-line {
    position: absolute; left: 0; width: 100%;
    text-align: center; font-weight: 900; white-space: nowrap;
  }
  .title-the { top: 36px; font-size: 66px; line-height: 66px; color: var(--navy); }
  .title-main { top: 102px; font-size: 82px; line-height: 82px; color: var(--navy); }
  .title-accent { top: 182px; font-size: 102px; line-height: 102px; color: var(--green); }
  .subtitle {
    position: absolute; top: 302px; left: 0; width: 100%;
    text-align: center; font-size: 33px; line-height: 44px;
    color: var(--ink); font-weight: 400;
  }
  .subtitle strong { font-weight: 800; }
  .food-spread { position: absolute; filter: blur(8px); opacity: .8; }
  .food-left {
    left: -20px; top: 520px; width: 340px; height: 400px;
    border-radius: 40% 50% 30% 20%;
    background: linear-gradient(160deg, #a9c77a, #e0a070 35%, #c9939a 60%, #e4d6bf);
  }
  .food-right {
    right: -20px; top: 470px; width: 340px; height: 420px;
    border-radius: 50% 30% 20% 45%;
    background: linear-gradient(200deg, #f1efe8, #8fbf6a 30%, #df7a66 55%, #e2d2b8);
  }
  .tiers { position: absolute; left: 0; top: 0; width: 800px; height: 1200px; }
  .tier-label {
    font-family: "Montserrat", sans-serif; font-weight: 800; font-size: 20px;
    fill: var(--white); text-anchor: middle;
  }
  .author {
    position: absolute; top: 1109px; left: 0; width: 100%; text-align: center;
    font-size: 27px; line-height: 27px; font-weight: 500; letter-spacing: 6px;
    padding-left: 6px; color: var(--ink);
  }
</style>
</head>
<body>
<main class="cover">
  <h1>
    <span class="title-line title-the">THE</span>
    <span class="title-line title-main">PLATE</span>
    <span class="title-line title-accent">COMPASS</span>
  </h1>
  <p class="subtitle">Cutting Through the Noise to What<br><strong>Actually Works.</strong></p>

  <div class="food-spread food-left" role="img" aria-label="Photo of fresh whole foods: vegetables, grains, legumes, nuts and raw meat"></div>
  <div class="food-spread food-right" role="img" aria-label="Photo of fresh whole foods: tomatoes, broccoli, peppers, dairy and raw meat"></div>

  <svg class="tiers" viewBox="0 0 800 1200" role="img" aria-label="Six stacked tiers of nutrition priorities, from calories at the top to noise at the base">
    <polygon points="345,470 435,470 485,558 295,558" fill="var(--tier-1)"/>
    <text class="tier-label" x="390" y="521">Calories</text>

    <polygon points="290,566 490,566 540,654 240,654" fill="var(--tier-2)"/>
    <text class="tier-label" x="390" y="617">Protein</text>

    <polygon points="236,662 544,662 595,750 185,750" fill="var(--tier-3)"/>
    <text class="tier-label" x="390" y="713">Food Quality</text>

    <polygon points="181,758 599,758 649,846 131,846" fill="var(--tier-4)"/>
    <text class="tier-label" x="390" y="809">Meal Timing</text>

    <polygon points="126,854 654,854 704,942 76,942" fill="var(--tier-5)"/>
    <text class="tier-label" x="390" y="905">Supplements</text>

    <polygon points="71,950 709,950 759,1038 21,1038" fill="var(--tier-6)"/>
    <text class="tier-label" x="390" y="1001">Noise</text>
  </svg>

  <p class="author">AUTHOR NAME</p>
</main>
</body>
</html>
```